Business Cards Needed for Innovative Healthcare Marketing Company

We are a marketing company focused on healthcare. Our company is all about rebranding yourself renewing your image and generating results. The phoenix stands for "reborn" or "rising" which we provide new brands for our clients we take their old brands and renew it with creativity and innovation. I am looking for a business card with color dimension. I have attached an example of a card I think has the look and feel of what I am trying to accomplish. I like that the card example has black and grey font colors, I like the font placement and the small logo, I really like the use of the colors on the right those are the colors of my logo. My logo is phoenix so maybe incorporating flames similar to that design. I would like the back a solid color maybe red with an opaque version of the logo and website. As a marketing company I am always open to creative liberty!

Target Market(s)

Doctors and business professionals.

Industry/Entity Type

Marketing

Contact Information for Business Card

Valcorne Health Care Marketing
Marla Tenwick- CEO
#(512)638-2974
email-marla@valcorne.com
website- valcorne.com

Font styles to use
Sans Serif

Colors
ec1f27
f37122
ffc214
fbed22
fbf289
f04a50

Requirements
Must have
• The logo and required information
Nice to have
• icons by the information
Should not have
• child like font

```html
<!DOCTYPE html>
<html lang="en">
<head>
<meta charset="utf-8">
<title>Valcorne Health Care Marketing — Business Card</title>
<link rel="stylesheet" href="https://fonts.googleapis.com/css2?family=Open+Sans:ital,wght@0,400;0,600;0,700;1,400&display=swap">
<style>
  :root {
    --backdrop: #e9e9e9;
    --card-white: #f4f4f6;
    --brand-red: #8e1c1d;
    --brand-red-light: #a23a20;
    --brand-orange: #e5891f;
    --brand-gold: #f0b23a;
    --text-dark: #3c3c3c;
    --rule-grey: #9a9a9a;
    --white: #ffffff;
  }
  * { box-sizing: border-box; margin: 0; padding: 0; }
  html, body {
    width: 1105px; height: 1200px; overflow: hidden;
    background: var(--backdrop);
    font-family: "Open Sans", Arial, sans-serif;
  }
  .card {
    position: absolute; left: 180px;
    width: 745px; height: 428px;
    overflow: hidden;
  }
  /* Front */
  .card-front { top: 118px; background: var(--card-white); }
  .brand-lockup {
    position: absolute; left: 300px; top: 78px;
    display: flex; align-items: center; gap: 22px;
  }
  .brand-mark {
    width: 92px; height: 92px; border-radius: 50%;
    background: var(--brand-orange);
  }
  .brand-name {
    color: var(--brand-red);
    font-weight: 400; font-size: 30px; line-height: 1.15;
    letter-spacing: 1px; text-transform: uppercase;
    width: 330px;
  }
  .person-name {
    position: absolute; left: 55px; top: 245px;
    color: var(--brand-red);
    font-weight: 700; font-size: 25px; letter-spacing: 0.3px;
  }
  .person-title {
    position: absolute; left: 55px; top: 278px;
    color: var(--brand-orange);
    font-size: 19px;
  }
  .title-rule {
    position: absolute; left: 105px; top: 292px;
    width: 577px; height: 1px; background: var(--rule-grey);
  }
  .contact-list { position: absolute; left: 55px; top: 318px; list-style: none; }
  .contact-item {
    display: flex; align-items: center; gap: 14px;
    color: var(--text-dark); font-size: 19px; line-height: 28px;
  }
  .contact-icon { width: 18px; height: 18px; fill: var(--brand-red); }
  .website-front {
    position: absolute; right: 62px; top: 340px;
    color: var(--text-dark); font-size: 19px;
  }
  .edge-band {
    position: absolute; left: 0; bottom: 0; width: 100%; height: 20px;
    background: var(--brand-red);
    border-top: 3px solid var(--brand-gold);
  }
  /* Back */
  .card-back {
    top: 636px;
    background: linear-gradient(180deg, var(--brand-red-light) 0%, var(--brand-red) 45%, var(--brand-red) 100%);
    display: flex; flex-direction: column; align-items: center;
  }
  .back-brand {
    margin-top: 150px;
    color: var(--white);
    font-size: 40px; font-weight: 400; letter-spacing: 4px;
    text-transform: uppercase;
  }
  .website-back {
    position: absolute; top: 362px; width: 100%; text-align: center;
    color: var(--white); font-style: italic; font-size: 19px;
    letter-spacing: 6px;
  }
</style>
</head>
<body>
  <section class="card card-front">
    <div class="brand-lockup">
      <div class="brand-mark"></div>
      <div class="brand-name">Valcorne Health Care Marketing</div>
    </div>
    <h1 class="person-name">MARLA TENWICK</h1>
    <p class="person-title">CEO</p>
    <div class="title-rule"></div>
    <ul class="contact-list">
      <li class="contact-item">
        <svg class="contact-icon" viewBox="0 0 24 24" aria-hidden="true"><path d="M6.6 10.8a15.1 15.1 0 0 0 6.6 6.6l2.2-2.2a1 1 0 0 1 1-.25 11.4 11.4 0 0 0 3.6.57 1 1 0 0 1 1 1V20a1 1 0 0 1-1 1A17 17 0 0 1 3 4a1 1 0 0 1 1-1h3.5a1 1 0 0 1 1 1c0 1.25.2 2.45.57 3.57a1 1 0 0 1-.25 1z"/></svg>
        (512)638-2974
      </li>
      <li class="contact-item">
        <svg class="contact-icon" viewBox="0 0 24 24" aria-hidden="true"><path d="M2 5h20v14H2z M2 5l10 8 10-8" /></svg>
        marla@valcorne.com
      </li>
    </ul>
    <p class="website-front">www.valcorne.com</p>
    <div class="edge-band"></div>
  </section>

  <section class="card card-back">
    <div class="back-brand">Valcorne</div>
    <p class="website-back">www.valcorne.com</p>
  </section>
</body>
</html>
```